Design Website Templates for Photographers for Lumera Inc. (trylumera.example)

Lumera Inc. is a generative website company for wedding photographers.
We are seeking new photography website design inspirations for the next template to be offered on our platform. The catch is you must use the same data for your designs. You also must use all of the data somewhere in the design. You cannot add new content besides the data available. If you wish to add any elements It will be hardcoded and must be universally fitting for many different photographers. We recommend not using any hardcoded test.
Don't be afraid to be creative! Although the most important element of a photographers website is the photos, we are looking for unique and out-of-the-box designs for the actual site as well.
Here is the User generated data available to you:
- 4 Hero Images Landscape, 4 Hero Images Portrait
- Tagline “destination photographer based in Maui, Hawaii”
- “About Photo” of the photographer
- “About” Biography Text
- The design can use up to 3 colors + background color and 2 fonts
- 9 Gallery images
- 3 Packages/services that include landscape/portrait images, a price, a title and text
- Testimonials made up of an image, text and text for the name of testimonial giver
See some examples of our current website designs attached. You can use any of the data you see in the designs.
Updates
We are looking for designs that are less feminine and are more neutral in color and fonts. Currently our templates are more oriented towards feminine photographers. We want to have designs that speak to diverse audiences. We thank everyone for submitting and are reviewing the designs.
Number of Pages Required
1 page
Look and feel
Each slider illustrates characteristics of the customer's brand and the style your logo design should communicate.

```html
<!DOCTYPE html>
<html lang="en">
<head>
<meta charset="UTF-8">
<title>Lumera — Destination Photographer</title>
<link href="https://fonts.googleapis.com/css2?family=Poppins:wght@400;500;600;700;800&display=swap" rel="stylesheet">
<style>
:root{
  --accent:#e8a33a;
  --teal:#7fe3e3;
  --teal-text:#5fe0d8;
  --ink:#1b1b1b;
  --black:#000;
  --white:#fff;
  --grey:#6b6b6b;
  --line:#8a8a8a;
}
*{box-sizing:border-box;margin:0;padding:0}
html,body{width:1200px;height:4827px;overflow:hidden;background:var(--white)}
body{position:relative;font-family:'Poppins',sans-serif;color:var(--ink)}
.abs{position:absolute}
.photo{position:absolute;overflow:hidden}

/* hero */
.hero{left:0;top:0;width:1200px;height:596px;background:linear-gradient(120deg,#6f6a4c 0%,#9b8f6a 35%,#b7a98a 55%,#7d7457 80%,#5e5a44 100%)}
.logo-badge{left:116px;top:14px;width:168px;height:168px;border-radius:50%;background:rgba(60,55,45,.55);display:flex;align-items:center;justify-content:center}
.logo-badge span{color:var(--white);font-weight:500;font-size:36px;letter-spacing:2px}
.nav{left:401px;top:46px;display:flex;gap:17px;font-size:14px;font-weight:500;color:var(--white);text-transform:uppercase}
.btn-book{left:872px;top:28px;width:214px;height:51px;border:1.5px solid rgba(255,255,255,.85);color:var(--white);font-size:16px;display:flex;align-items:center;justify-content:center}
.tagline-panel{left:596px;top:337px;width:604px;height:259px;background:rgba(40,40,30,.35);border-top-left-radius:18px}
.tagline{left:610px;top:360px;font-weight:800;font-size:45px;line-height:62px;color:var(--teal-text);text-transform:uppercase}

/* about */
.eyebrow{font-size:27px;font-weight:500;color:var(--accent);text-transform:uppercase}
.heading{font-size:37px;font-weight:700;color:var(--accent);text-transform:uppercase}
.body-text{font-size:20.5px;line-height:36px;text-align:justify;color:var(--ink)}
.btn-outline{border:1.5px solid #555;color:var(--accent);font-size:17px;display:flex;align-items:center;justify-content:center;text-transform:uppercase}
.frame-tr{border-top:7px solid var(--teal);border-right:7px solid var(--teal);border-top-right-radius:40px;border-top-left-radius:40px;border-bottom-right-radius:40px}
.frame-bl{border-left:7px solid var(--teal);border-bottom:7px solid var(--teal);border-bottom-left-radius:40px;border-top-left-radius:40px;border-bottom-right-radius:40px}
.card{background:var(--white);border-radius:24px;box-shadow:0 2px 14px rgba(0,0,0,.18)}

/* sections */
.section-title{left:0;width:1200px;text-align:center;font-size:37px;font-weight:700;color:var(--accent);text-transform:uppercase}
.gallery-glow{left:260px;top:2300px;width:680px;height:660px;background:radial-gradient(ellipse at center,rgba(127,227,227,.9) 0%,rgba(127,227,227,.5) 45%,rgba(127,227,227,0) 75%)}
.tile{border-radius:14px}

.pkg-bracket{border:3px solid var(--accent);border-top:none;border-radius:0 0 14px 14px}
.pkg-label{background:var(--white);border-radius:8px;box-shadow:0 2px 10px rgba(0,0,0,.18);display:flex;flex-direction:column;align-items:center;justify-content:center;font-size:17px;text-transform:uppercase;text-align:center;line-height:22px}
.pkg-label .price{text-transform:none;margin-top:12px}

/* testimonials & footer */
.dark{left:0;top:4127px;width:1200px;height:700px;background:var(--black)}
.quote-frame{left:362px;top:3984px;width:476px;height:366px;border:6px solid var(--grey);border-radius:30px}
.avatar{left:514px;top:3996px;width:172px;height:172px;border-radius:50%;background:linear-gradient(#f4f4f4,#d8d8d8);box-shadow:0 2px 12px rgba(0,0,0,.25)}
.quote-name{left:362px;width:476px;top:4178px;text-align:center;color:var(--white);font-weight:600;font-size:21px}
.quote-text{left:405px;width:390px;top:4228px;text-align:justify;text-align-last:justify;color:var(--white);font-size:17px;line-height:30px}
.stars{left:362px;width:476px;top:4292px;display:flex;justify-content:center;gap:14px}
.arrow{width:68px;height:68px;border-radius:50%;background:var(--white);display:flex;align-items:center;justify-content:center}

.foot-title{color:var(--white);font-weight:700;font-size:17px;text-transform:uppercase;text-align:center}
.foot-links{color:var(--white);font-size:19px;line-height:34.5px;text-align:center}
.foot-logo{left:496px;width:200px;top:4510px;text-align:center;color:var(--white);font-size:38px;font-weight:500;letter-spacing:2px}
.social{left:506px;top:4583px;width:184px;height:60px;border:1.5px solid var(--white);border-radius:30px;display:flex;align-items:center;justify-content:center;gap:40px}
.social span{width:16px;height:16px;border-radius:50%;background:var(--white)}
.copyright{left:0;width:1200px;top:4758px;text-align:center;color:var(--white);font-size:17px}
</style>
</head>
<body>

<!-- Hero -->
<div class="photo hero" role="img" aria-label="Hero photo: photographer shooting a couple on a grassy hillside"></div>
<div class="abs logo-badge"><span>LUMERA</span></div>
<nav class="abs nav"><span>About</span><span>Blog</span><span>Testimonials</span><span>Portfolio</span><span>Get in touch</span></nav>
<div class="abs btn-book">BOOK NOW</div>
<div class="abs tagline-panel"></div>
<h1 class="abs tagline">Destination<br>photographer<br>based in Maui, Hawaii</h1>

<!-- About photographer -->
<div class="abs eyebrow" style="left:116px;top:702px">About</div>
<h2 class="abs heading" style="left:116px;top:738px">Photographer</h2>
<p class="abs body-text" style="left:129px;top:795px;width:402px">Lorem ipsum dolor sit amet, consectetur adipiscing elit, sed do eiusmod tempor incididunt ut labore et dolore magna aliqua. Ut enim ad minim veniam, quis nostrud exercitation ullamco laboris nisi ut aliquip ex ea commodo consequat. Duis aute irure dolor in reprehenderit in</p>
<div class="abs btn-outline" style="left:129px;top:1099px;width:257px;height:62px">Read more</div>
<div class="abs frame-tr" style="left:996px;top:643px;width:193px;height:219px"></div>
<div class="photo" style="left:834px;top:681px;width:314px;height:371px;border-radius:28px 0 28px 28px;background:linear-gradient(135deg,#d9d6cf,#6a6a64 55%,#2a2a28)" role="img" aria-label="Camera screen showing a wedding couple"></div>
<div class="abs frame-bl" style="left:544px;top:1059px;width:154px;height:179px"></div>
<div class="photo" style="left:578px;top:915px;width:247px;height:293px;border-radius:26px 0 26px 0;background:linear-gradient(135deg,#f1ece6,#b9aaa0 50%,#3a3836)" role="img" aria-label="Hands holding a camera framing a heart"></div>

<!-- About photo -->
<div class="abs eyebrow" style="left:116px;top:1390px">About</div>
<h2 class="abs heading" style="left:116px;top:1428px">Photo</h2>
<p class="abs body-text" style="left:122px;top:1497px;width:469px">Lorem ipsum dolor sit amet, consectetur adipiscing elit, sed do eiusmod tempor incididunt ut labore et dolore magna aliqua. Ut enim ad minim veniam, quis nostrud exercitation ullamco laboris nisi ut aliquip ex ea commodo consequat. Duis aute irure dolor in reprehenderit in voluptate velit esse cillum dolore eu fugiat nulla pariatur. Excepteur sint</p>
<div class="abs btn-outline" style="left:126px;top:1828px;width:257px;height:62px">Read more</div>
<div class="abs card" style="left:602px;top:1365px;width:427px;height:268px"></div>
<div class="photo" style="left:624px;top:1378px;width:386px;height:242px;border-radius:20px;background:linear-gradient(180deg,#cfd3d6,#8d96a0 50%,#b7b2aa)" role="img" aria-label="Photographer shooting a couple on the beach"></div>
<div class="abs card" style="left:662px;top:1693px;width:424px;height:266px"></div>
<div class="photo" style="left:684px;top:1706px;width:382px;height:240px;border-radius:20px;background:linear-gradient(180deg,#6fa6d8,#b9d3ea 45%,#d8b98a 70%,#c79a64)" role="img" aria-label="Wedding couple seen through a frame on the beach"></div>

<!-- Gallery -->
<h2 class="abs section-title" style="top:2122px">Gallery</h2>
<div class="abs gallery-glow"></div>
<div class="photo tile" style="left:0;top:2231px;width:384px;height:261px;background:linear-gradient(135deg,#b9b3a8,#8f8678 60%,#6d6458)" role="img" aria-label="Couple posing behind a gilded frame"></div>
<div class="photo tile" style="left:399px;top:2231px;width:402px;height:261px;background:linear-gradient(135deg,#c7d0b0,#8f9a77 50%,#f0ede8)" role="img" aria-label="Couple looking at a camera"></div>
<div class="photo tile" style="left:816px;top:2231px;width:384px;height:261px;background:linear-gradient(135deg,#e1b46a,#9e8a5a 50%,#6c6e48)" role="img" aria-label="Couple on a sunlit hillside"></div>
<div class="photo tile" style="left:0;top:2507px;width:384px;height:259px;background:linear-gradient(135deg,#4a3220,#7d5638 50%,#3a2718)" role="img" aria-label="Bride lying on a wooden floor"></div>
<div class="photo tile" style="left:399px;top:2507px;width:402px;height:259px;background:linear-gradient(180deg,#6d4a32,#8a5e3e 50%,#5c3d28)" role="img" aria-label="Wooden wall decorated with flowers and lights"></div>
<div class="photo tile" style="left:816px;top:2507px;width:384px;height:259px;background:linear-gradient(180deg,#3e4a30,#8b8a6a 50%,#c9b894)" role="img" aria-label="Couple on a lakeside pier at sunset"></div>
<div class="photo tile" style="left:0;top:2782px;width:384px;height:257px;background:linear-gradient(180deg,#2d2824,#5c4a3a 50%,#3a2e26)" role="img" aria-label="Reception tables under string lights"></div>
<div class="photo tile" style="left:399px;top:2782px;width:402px;height:257px;background:linear-gradient(135deg,#3a2a6a,#7a4ab0 50%,#2a1f4a)" role="img" aria-label="Banquet table lit in purple"></div>
<div class="photo tile" style="left:816px;top:2782px;width:384px;height:257px;background:linear-gradient(135deg,#2f2e2c,#7a6a5e 50%,#e8e4de)" role="img" aria-label="Wedding rings on a flower"></div>

<!-- Packages -->
<h2 class="abs section-title" style="top:3240px">Packages</h2>

<div class="abs pkg-bracket" style="left:148px;top:3619px;width:210px;height:79px"></div>
<div class="photo" style="left:111px;top:3354px;width:285px;height:278px;background:linear-gradient(180deg,#5a4a34,#8a7a5a 50%,#c9bfae)" role="img" aria-label="Floral wedding arch in a forest"></div>
<div class="abs pkg-label" style="left:163px;top:3578px;width:182px;height:108px"><span>Wedding</span><span class="price">$ 12.000</span></div>

<div class="abs pkg-bracket" style="left:495px;top:3619px;width:210px;height:79px"></div>
<div class="photo" style="left:458px;top:3354px;width:285px;height:278px;background:linear-gradient(180deg,#e6e4e0,#bdb8ae 50%,#8e8a80)" role="img" aria-label="Bride in front of a classic building"></div>
<div class="abs pkg-label" style="left:510px;top:3578px;width:182px;height:108px"><span>Wedding</span><span class="price">$ 12.000</span></div>

<div class="abs pkg-bracket" style="left:841px;top:3619px;width:210px;height:79px"></div>
<div class="photo" style="left:804px;top:3354px;width:285px;height:278px;background:linear-gradient(135deg,#5a3a52,#c9b07a 50%,#e4e2dc)" role="img" aria-label="Restaurant buffet table"></div>
<div class="abs pkg-label" style="left:856px;top:3578px;width:182px;height:108px"><span>Restaurant<br>Buffet</span><span class="price">$ 12.000</span></div>

<!-- Testimonials -->
<h2 class="abs section-title" style="top:3898px">Testimonials</h2>
<div class="abs dark"></div>
<div class="abs quote-frame"></div>
<div class="abs avatar" role="img" aria-label="Portrait of the client giving the testimonial"></div>
<div class="abs quote-name">Lorem ipsum</div>
<p class="abs quote-text">Lorem ipsum dolor sit amet, consectetur adipiscing elit, sed do eiusmod tempor</p>
<div class="abs stars">
  <svg width="22" height="22" viewBox="0 0 24 24"><path fill="#f5b400" d="M12 2l3 6.6 7 .7-5.3 4.8 1.6 7L12 17.6 5.7 21.1l1.6-7L2 9.3l7-.7z"/></svg>
  <svg width="22" height="22" viewBox="0 0 24 24"><path fill="#f5b400" d="M12 2l3 6.6 7 .7-5.3 4.8 1.6 7L12 17.6 5.7 21.1l1.6-7L2 9.3l7-.7z"/></svg>
  <svg width="22" height="22" viewBox="0 0 24 24"><path fill="#f5b400" d="M12 2l3 6.6 7 .7-5.3 4.8 1.6 7L12 17.6 5.7 21.1l1.6-7L2 9.3l7-.7z"/></svg>
  <svg width="22" height="22" viewBox="0 0 24 24"><path fill="#f5b400" d="M12 2l3 6.6 7 .7-5.3 4.8 1.6 7L12 17.6 5.7 21.1l1.6-7L2 9.3l7-.7z"/></svg>
  <svg width="22" height="22" viewBox="0 0 24 24"><path fill="#f5b400" d="M12 2l3 6.6 7 .7-5.3 4.8 1.6 7L12 17.6 5.7 21.1l1.6-7L2 9.3l7-.7z"/></svg>
</div>
<div class="abs arrow" style="left:114px;top:4226px"><svg width="30" height="30" viewBox="0 0 24 24"><path d="M15 4l-8 8 8 8" fill="none" stroke="#000" stroke-width="1.6"/></svg></div>
<div class="abs arrow" style="left:1018px;top:4226px"><svg width="30" height="30" viewBox="0 0 24 24"><path d="M9 4l8 8-8 8" fill="none" stroke="#000" stroke-width="1.6"/></svg></div>

<!-- Footer -->
<div class="abs foot-title" style="left:112px;width:240px;top:4537px">Quick links</div>
<div class="abs foot-links" style="left:112px;width:240px;top:4600px">Home<br>About Us<br>Services<br>Contact Us</div>
<div class="abs foot-logo">LUMERA</div>
<div class="abs social"><span></span><span></span><span></span></div>
<div class="abs foot-title" style="left:801px;width:300px;top:4522px">Services</div>
<p class="abs foot-links" style="left:801px;width:300px;top:4583px;font-size:18.5px">Lorem ipsum dolor sit amet, consectetur adipiscing elit, sed do eiusmod tempor incididunt ut labore et</p>
<div class="abs copyright">CopyRight@2023 Lumera | All Right Reserved</div>

</body>
</html>
```